Modern Verdell Tree Care Website

I need a website for a full service Tree Care company. The company provides tree pruning, tree removal, tree preservation, emergency services, stump grinding, and emergency tree services.

Target Market(s)

Customers that need tree services

Industry/Entity Type

Landscaping, Tree Services

Coding

Coded - Design and coding required

Number of Pages Required

5+ page

Font styles to use
Sans Serif

Requirements
Must have
• Good clean design that showcases the services the company provides.
Nice to have
• Services page; contact form, blog, home page, about page

```html
<!DOCTYPE html>
<html lang="en">
<head>
<meta charset="utf-8">
<title>Verdell Tree Care — Website Design</title>
<link rel="stylesheet" href="https://fonts.googleapis.com/css2?family=Poppins:wght@400;500;600;700&display=swap">
<style>
:root{
  --green:#2db93b;
  --green-dark:#1f8f2c;
  --sage:#e6ebdf;
  --sage-tile:#e9eee3;
  --ink:#2a3a2c;
  --muted:#5d665e;
  --orange:#f39a1e;
  --white:#ffffff;
  --blue:#2f8ff0;
  --page:#ffffff;
}
*{box-sizing:border-box;margin:0;padding:0}
html,body{width:1200px;height:1200px;overflow:hidden;background:var(--page)}
body{font-family:"Poppins",Arial,sans-serif;color:var(--ink)}
.stage{position:absolute;left:0;top:0;width:1000px;height:1000px;transform:scale(1.2);transform-origin:0 0}
.column{position:absolute;width:448px;overflow:hidden;background:var(--white)}
.column--left{left:35px;top:0;height:1000px;background:transparent}
.column--right{left:516px;top:0;height:963px}
.abs{position:absolute}
.photo{position:absolute;display:block;overflow:hidden}
.small{font-size:4px;line-height:1.45;color:var(--muted)}
.nowrap{white-space:nowrap}

/* hero */
.hero{left:0;top:32px;width:448px;height:228px;
  background:
    radial-gradient(ellipse 30% 45% at 38% 28%,rgba(255,240,160,.65),transparent 70%),
    linear-gradient(90deg,rgba(30,45,15,.35),transparent 20%,transparent 80%,rgba(30,45,15,.4)),
    linear-gradient(180deg,#93ad45 0%,#5f8128 42%,#3c5c1c 75%,#2b4416 100%)}
.nav{left:45px;top:52px;width:357px;height:20px;background:rgba(255,255,255,.92)}
.brand{position:absolute;left:4px;top:0;height:20px;display:flex;align-items:center;gap:3px;font-weight:700;font-size:7px;color:var(--green-dark);white-space:nowrap}
.brand-mark{width:8px;height:8px;background:var(--green);flex:none}
.nav-links{position:absolute;left:104px;top:0;height:20px;display:flex;align-items:center;gap:24px;font-size:4.4px;color:var(--ink);white-space:nowrap}
.nav-cta{position:absolute;right:0;top:0;height:20px;width:64px;background:var(--orange);color:var(--ink);font-size:4.4px;font-weight:600;display:flex;align-items:center;justify-content:center;white-space:nowrap}
.hero-title{left:0;top:133px;width:448px;text-align:center;color:var(--white);font-weight:700;font-size:14px;line-height:1.2}
.hero-title .accent{color:var(--orange)}
.hero-sub{left:0;top:167px;width:448px;text-align:center;color:var(--white);font-weight:600;font-size:5.5px;letter-spacing:1.2px;white-space:nowrap}

/* who we are */
.about{left:45px;top:230px;width:357px;height:225px;background:var(--sage)}
.about h2{position:absolute;left:37px;top:11px;font-size:12px;font-weight:700}
.about-copy{position:absolute;left:37px;top:30px;width:148px}
.about-copy p+p{margin-top:3px}
.estimate{position:absolute;left:220px;top:35px;text-align:right;width:100px}
.estimate-label{font-size:4.6px;font-weight:600;color:var(--ink);white-space:nowrap}
.phone{font-size:10px;font-weight:600;color:var(--orange);line-height:1.2;display:flex;align-items:center;justify-content:flex-end;gap:2px;white-space:nowrap}
.about-rule{position:absolute;left:37px;top:80px;width:283px;height:1px;background:#cfd6c7}
.what{position:absolute;left:37px;top:93px;font-size:6px;font-weight:600}
.service-card{position:absolute;top:110px;width:89px}
.service-card .photo{position:relative;width:89px;height:50px}
.service-card h4{font-size:4.6px;font-weight:700;margin-top:8px;white-space:nowrap}
.service-card .small{margin-top:1px}
.full-list{display:inline-block;margin-top:6px;font-size:3.8px;border-bottom:1px solid var(--ink);padding-bottom:1px;font-weight:500}

.features{left:45px;top:455px;width:357px;height:45px;background:var(--green)}
.feature{position:absolute;top:15px;display:grid;grid-template-columns:12px auto;column-gap:4px;align-items:center;color:var(--white);white-space:nowrap}
.feature svg{grid-row:1 / span 2}
.feature strong{font-size:4.2px;font-weight:600;line-height:1.3}
.feature span{font-size:3.6px;opacity:.9;line-height:1.3}

/* expertise */
.kicker{font-size:4px;color:var(--muted)}
.expertise{left:82px;top:536px;width:142px}
.expertise h2{font-size:7.6px;font-weight:700;line-height:1.3;margin-top:5px}
.expertise h2 em{font-style:normal;color:var(--green)}
.ticks{list-style:none;margin-top:6px}
.ticks li{display:flex;align-items:center;gap:3px;font-size:4.2px;color:var(--muted);line-height:1.9;white-space:nowrap}
.play{position:absolute;left:59px;top:32px;width:15px;height:15px;border-radius:50%;background:var(--green)}

/* services */
.services-photo{width:138px;height:137px;
  background:
    radial-gradient(ellipse 40% 30% at 50% 12%,rgba(230,140,70,.55),transparent 70%),
    radial-gradient(ellipse 35% 50% at 50% 55%,rgba(40,70,30,.55),transparent 70%),
    linear-gradient(160deg,#a2b95c,#58802e 55%,#2d4018)}
.services-title{position:absolute;left:0;width:138px;text-align:center;color:var(--white);font-weight:700;font-size:15px;line-height:1.3}
.services-sub{position:absolute;left:0;width:138px;text-align:center;color:var(--white);font-size:4px}
.tile{position:absolute;width:66px;height:62px;background:var(--sage-tile);display:flex;flex-direction:column;align-items:center;justify-content:center;gap:6px}
.tile-icon{width:24px;height:22px}
.tile-label{font-size:3.8px;font-weight:500;color:var(--ink);white-space:nowrap}

/* recent work */
.band{position:absolute;left:0;width:448px;background:var(--green)}
.band h2{position:absolute;left:82px;color:var(--white);font-size:11px;font-weight:700;line-height:1.25}
.band p{position:absolute;left:229px;width:140px;font-size:4.2px;line-height:1.55;color:var(--white)}
.compare{position:absolute;left:82px;width:283px;height:151px}
.compare .photo{top:0;height:151px;width:141px}
.before{background:
  radial-gradient(ellipse 60% 25% at 40% 20%,rgba(140,70,80,.45),transparent 70%),
  linear-gradient(180deg,#3f5e27 0%,#4e7a2e 40%,#2f4a1d 100%)}
.after{background:
  radial-gradient(ellipse 50% 15% at 50% 17%,rgba(230,110,110,.7),transparent 70%),
  radial-gradient(ellipse 35% 45% at 85% 70%,rgba(210,170,210,.8),transparent 70%),
  radial-gradient(ellipse 25% 35% at 10% 60%,rgba(200,170,220,.6),transparent 70%),
  linear-gradient(180deg,#3f6a2a 0%,#6aa53a 30%,#58a032 70%,#3e7a25 100%)}
.handle{position:absolute;left:137px;top:71px;width:9px;height:9px;border-radius:50%;background:var(--white);border:1px solid #ccc}

/* gallery */
.thumb{width:65px;height:65px}
.projects{left:229px;top:431px;width:136px;height:138px;
  background:
    radial-gradient(ellipse 30% 12% at 45% 52%,rgba(255,210,120,.8),transparent 70%),
    radial-gradient(ellipse 40% 15% at 60% 85%,rgba(230,200,90,.5),transparent 70%),
    linear-gradient(180deg,#2b3d62,#55638a 38%,#3a5a2b 68%,#2e4a1e)}
.projects-title{position:absolute;left:229px;top:484px;width:136px;text-align:center;color:var(--white);font-size:15px;font-weight:700;line-height:1.3}
.projects-sub{position:absolute;left:229px;top:508px;width:136px;text-align:center;color:var(--white);font-size:4px}

/* estimate form */
.quote{left:0;top:601px;width:259px;height:200px;background:var(--green)}
.quote h2{position:absolute;left:83px;top:38px;color:var(--white);font-size:12px;font-weight:600;white-space:nowrap}
.form-label{position:absolute;color:var(--white);font-size:4.6px;font-weight:600;white-space:nowrap}
.field{position:absolute;left:83px;width:102px;height:10px;background:var(--white);font-size:3.6px;color:#999;padding:2px 3px}
.check{position:absolute;left:192px;display:flex;align-items:center;gap:4px;color:var(--white);font-size:3.8px;white-space:nowrap}
.check i{width:6px;height:6px;background:var(--white);display:block}
.submit{position:absolute;left:83px;top:748px;width:46px;height:13px;background:var(--blue);color:var(--white);font-size:3.8px;display:flex;align-items:center;justify-content:center;white-space:nowrap}
.worker{left:259px;top:601px;width:189px;height:200px;
  background:
    radial-gradient(ellipse 25% 40% at 50% 55%,rgba(225,232,240,.55),transparent 70%),
    radial-gradient(ellipse 40% 30% at 15% 20%,rgba(240,150,60,.8),transparent 70%),
    radial-gradient(ellipse 35% 30% at 85% 30%,rgba(190,60,50,.6),transparent 70%),
    linear-gradient(160deg,#d8803a,#9e4a2a 35%,#5e7a33 65%,#3d5a22)}

/* footer */
.footer{left:0;top:801px;width:448px;height:162px;background:var(--sage)}
.cta{position:absolute;left:83px;top:27px;width:282px;height:36px;background:var(--white);display:flex;align-items:center;justify-content:space-between;padding:0 12px}
.cta-text{font-size:7.6px;color:var(--ink);white-space:nowrap}
.cta-btn{width:58px;height:11px;background:var(--blue);color:var(--white);font-size:3.6px;display:flex;align-items:center;justify-content:center;white-space:nowrap}
.foot-col{position:absolute;top:78px;width:62px}
.foot-col h5{font-size:4.8px;font-weight:500;color:var(--ink);margin-bottom:6px;white-space:nowrap}
.foot-link{font-size:3.4px;color:var(--muted);border-bottom:1px solid #cfd5c8;padding:2px 0 3px}
.foot-line{display:flex;align-items:center;gap:3px;font-size:3.4px;color:var(--muted);line-height:2.2;white-space:nowrap}
.socials{display:flex;gap:3px;margin-top:4px}
.socials i{width:8px;height:8px;border:1px solid var(--green);border-radius:50%;display:block}
.foot-brand{position:absolute;left:297px;top:118px;display:flex;align-items:center;gap:3px;font-size:7px;font-weight:700;color:var(--green-dark);white-space:nowrap}
</style>
</head>
<body>
<svg width="0" height="0" style="position:absolute" aria-hidden="true">
  <defs>
    <symbol id="icon-grass" viewBox="0 0 24 22">
      <g fill="none" stroke="#2db93b" stroke-width="1" stroke-linecap="round" stroke-linejoin="round">
        <path d="M2 18h20"/><path d="M3 21h18"/>
        <path d="M5 18c0-4 1-7 3-9"/><path d="M8 18c0-3-1-6-3-8"/>
        <path d="M11 18c0-5 1-9 3-12"/><path d="M14 18c0-4-1-7-3-9"/>
        <path d="M17 18c0-3 1-6 3-8"/><path d="M19 18c0-2-1-4-3-6"/>
      </g>
    </symbol>
    <symbol id="icon-lighting" viewBox="0 0 24 22">
      <g fill="none" stroke="#2db93b" stroke-width="1" stroke-linecap="round" stroke-linejoin="round">
        <path d="M9 20h6"/><path d="M12 20V10"/>
        <path d="M9 10h6l-1-4h-4z"/><path d="M10 6l2-2 2 2"/>
        <path d="M5 8h-2"/><path d="M21 8h-2"/><path d="M6 3l1.5 1.5"/><path d="M18 3l-1.5 1.5"/>
        <circle cx="19" cy="16" r="3"/><path d="M19 19v1"/>
      </g>
    </symbol>
    <symbol id="icon-hardscape" viewBox="0 0 24 22">
      <g fill="none" stroke="#2db93b" stroke-width="1" stroke-linejoin="round">
        <rect x="2" y="4" width="20" height="15"/>
        <path d="M2 9h20M2 14h20"/>
        <path d="M9 4v5M16 4v5M6 9v5M13 9v5M19 9v5M9 14v5M16 14v5"/>
      </g>
    </symbol>
    <symbol id="icon-landscape" viewBox="0 0 24 22">
      <g fill="none" stroke="#2db93b" stroke-width="1" stroke-linecap="round" stroke-linejoin="round">
        <circle cx="9" cy="8" r="5"/><path d="M9 13v7"/>
        <path d="M14 20c0-3 2-5 4.5-5S23 17 23 20"/>
        <path d="M1 20h22"/><path d="M7 8l2 2 2-3"/>
      </g>
    </symbol>
  </defs>
</svg>

<div class="stage">

  <!-- left page column -->
  <section class="column column--left">
    <div class="photo hero" role="img" aria-label="Sunlit pine forest with light rays through the trees"></div>
    <nav class="abs nav">
      <div class="brand"><span class="brand-mark"></span>Verdell Tree Care</div>
      <div class="nav-links"><span>About Us</span><span>Services</span><span>Charity</span><span>Career</span><span>Contact</span></div>
      <div class="nav-cta">Get a Free Quote</div>
    </nav>
    <h1 class="abs hero-title">CALL <span class="accent">VERDELL</span> FOR<br>ALL YOUR TREE CARE NEEDS</h1>
    <div class="abs hero-sub">SERVING BAYOU RIDGE AND SURROUNDING AREAS</div>

    <div class="abs about">
      <h2>Who We Are</h2>
      <div class="about-copy small">
        <p>At Verdell Tree Care, we are more than just a tree service company, we are stewards of our beautiful trees. With a passion rooted in arboriculture, we promote the health, beauty, and safety of your trees.</p>
        <p>Whether it's expert trimming, careful removal of hazards, or full tree health checks, we approach each task with dedication and attention to detail.</p>
      </div>
      <div class="estimate">
        <div class="estimate-label">TXT or CALL for a free estimate</div>
        <div class="phone">
          <svg width="6" height="8" viewBox="0 0 6 8"><rect x=".5" y=".5" width="5" height="7" rx="1" fill="none" stroke="#f39a1e"/></svg>(555) 204-7816
        </div>
        <div class="phone">(555) 318-4462</div>
      </div>
      <div class="about-rule"></div>
      <div class="what">What we do</div>

      <div class="service-card" style="left:37px">
        <div class="photo" role="img" aria-label="Hand pruning a branch with shears" style="background:radial-gradient(ellipse 30% 40% at 70% 55%,rgba(230,190,160,.8),transparent 70%),linear-gradient(135deg,#9cc064,#5a8a30 60%,#3f6a22)"></div>
        <h4>TREE PRUNING</h4>
        <p class="small">Careful cuts that shape growth, remove dead wood and keep each branch healthy.</p>
        <span class="full-list">Full List</span>
      </div>
      <div class="service-card" style="left:134px">
        <div class="photo" role="img" aria-label="Arborist cutting into a tree trunk" style="background:radial-gradient(ellipse 20% 40% at 30% 50%,rgba(220,200,150,.7),transparent 70%),linear-gradient(135deg,#b89a58,#8a6d36 55%,#5e4a24)"></div>
        <h4>TREE REMOVAL</h4>
        <p class="small">Safe removal of hazardous or dead trees, with full cleanup once the job is done.</p>
        <span class="full-list">Full List</span>
      </div>
      <div class="service-card" style="left:232px">
        <div class="photo" role="img" aria-label="Avenue of tall trimmed trees" style="background:linear-gradient(90deg,#4f8a2c,transparent 30%,transparent 70%,#4f8a2c),linear-gradient(180deg,#d4ecc0,#8cc25e 50%,#5f9a3a)"></div>
        <h4>TREE PRESERVATION</h4>
        <p class="small">Health checks, feeding and protection plans that help mature trees thrive.</p>
        <span class="full-list">Full List</span>
      </div>
    </div>

    <div class="abs features">
      <div class="feature" style="left:37px">
        <svg width="12" height="12" viewBox="0 0 12 12"><circle cx="6" cy="3.5" r="2.3" fill="none" stroke="#fff" stroke-width=".8"/><path d="M1.5 11c0-3 2.2-4.3 4.5-4.3s4.5 1.3 4.5 4.3" fill="none" stroke="#fff" stroke-width=".8"/></svg>
        <strong>Licensed Professionals</strong><span>Specializing in arborage</span>
      </div>
      <div class="feature" style="left:134px">
        <svg width="12" height="12" viewBox="0 0 12 12"><rect x="1" y="2" width="10" height="8.5" fill="none" stroke="#fff" stroke-width=".8"/><path d="M1 4.5h10" stroke="#fff" stroke-width=".8"/></svg>
        <strong>Online Service Booking</strong><span>Easy online, quick pricing</span>
      </div>
      <div class="feature" style="left:232px">
        <svg width="12" height="12" viewBox="0 0 12 12"><path d="M1 4.5h10v6H1zM3.5 4.5V2h5v2.5" fill="none" stroke="#fff" stroke-width=".8"/></svg>
        <strong>Premium Grass &amp; Plant Seeds</strong><span>We cover all aspects of tree work</span>
      </div>
    </div>

    <div class="abs expertise">
      <div class="kicker">Our Expertise</div>
      <h2>Thoughtful improvements to enrich your <em>residential</em> or <em>corporate</em> appearance</h2>
      <ul class="ticks">
        <li><svg width="5" height="5" viewBox="0 0 5 5"><path d="M.5 2.6l1.4 1.4L4.5 1" fill="none" stroke="#2db93b" stroke-width=".9"/></svg>5 Year Warranty on Workmanship</li>
        <li><svg width="5" height="5" viewBox="0 0 5 5"><path d="M.5 2.6l1.4 1.4L4.5 1" fill="none" stroke="#2db93b" stroke-width=".9"/></svg>Every Project is Run by a Team of Experts</li>
        <li><svg width="5" height="5" viewBox="0 0 5 5"><path d="M.5 2.6l1.4 1.4L4.5 1" fill="none" stroke="#2db93b" stroke-width=".9"/></svg>We Save You Time, Money, and Space</li>
      </ul>
    </div>
    <div class="photo" role="img" aria-label="Modern house with lit garden and reflecting pool at dusk" style="left:227px;top:530px;width:138px;height:80px;background:radial-gradient(ellipse 20% 40% at 88% 55%,rgba(240,170,90,.7),transparent 70%),linear-gradient(90deg,transparent 70%,rgba(120,70,50,.6)),linear-gradient(180deg,#4d5a6a,#6d7480 35%,#59683f 65%,#3f6a2b)">
      <span class="play"></span>
      <svg class="abs" style="left:64px;top:37px" width="6" height="6" viewBox="0 0 6 6"><path d="M1 .5L5.5 3 1 5.5z" fill="#fff"/></svg>
    </div>

    <div class="photo services-photo" role="img" aria-label="Gardener in apron holding a hedge trimmer" style="left:82px;top:643px"></div>
    <div class="services-title" style="left:82px;top:692px">Services</div>
    <div class="services-sub" style="left:82px;top:717px">Cost Calculation</div>
    <div class="tile" style="left:227px;top:643px"><svg class="tile-icon" role="img" aria-label="Grass installation icon"><use href="#icon-grass"/></svg><span class="tile-label">Grass Installation</span></div>
    <div class="tile" style="left:299px;top:643px"><svg class="tile-icon" role="img" aria-label="Landscape lighting icon"><use href="#icon-lighting"/></svg><span class="tile-label">Landscape Lighting</span></div>
    <div class="tile" style="left:227px;top:713px"><svg class="tile-icon" role="img" aria-label="Hardscaping icon"><use href="#icon-hardscape"/></svg><span class="tile-label">Hardscaping</span></div>
    <div class="tile" style="left:299px;top:713px"><svg class="tile-icon" role="img" aria-label="Landscaping icon"><use href="#icon-landscape"/></svg><span class="tile-label">Landscaping</span></div>

    <div class="band" style="top:813px;height:139px">
      <h2 style="top:31px">Our Most Recent<br>Work</h2>
      <p style="top:31px">Whether it is a courtyard or large space, we can design, landscape or maintain your garden to the highest standard. We use only the best materials. We aim to create a garden that you can enjoy wherever your specification to achieve a unique space.</p>
    </div>
    <div class="compare" style="top:893px">
      <div class="photo before" role="img" aria-label="Overgrown lawn before landscaping" style="left:0"></div>
      <div class="photo after" role="img" aria-label="Finished garden path with flower beds" style="left:142px"></div>
      <span class="handle"></span>
    </div>
  </section>

  <!-- right page column -->
  <section class="column column--right">
    <div class="photo services-photo" role="img" aria-label="Gardener in apron holding a hedge trimmer" style="left:82px;top:0;height:139px"></div>
    <div class="services-title" style="left:82px;top:53px">Services</div>
    <div class="services-sub" style="left:82px;top:78px">Cost Calculation</div>
    <div class="tile" style="left:227px;top:2px"><svg class="tile-icon" role="img" aria-label="Grass installation icon"><use href="#icon-grass"/></svg><span class="tile-label">Grass Installation</span></div>
    <div class="tile" style="left:300px;top:2px"><svg class="tile-icon" role="img" aria-label="Landscape lighting icon"><use href="#icon-lighting"/></svg><span class="tile-label">Landscape Lighting</span></div>
    <div class="tile" style="left:227px;top:72px"><svg class="tile-icon" role="img" aria-label="Hardscaping icon"><use href="#icon-hardscape"/></svg><span class="tile-label">Hardscaping</span></div>
    <div class="tile" style="left:300px;top:72px"><svg class="tile-icon" role="img" aria-label="Landscaping icon"><use href="#icon-landscape"/></svg><span class="tile-label">Landscaping</span></div>

    <div class="band" style="top:173px;height:138px">
      <h2 style="top:30px">Our Most Recent<br>Work</h2>
      <p style="top:30px">Whether it is a courtyard or large space, we can design, landscape or maintain your garden to the highest standard. We use only the best materials. We aim to create a garden that you can enjoy wherever your specification to achieve a unique space.</p>
    </div>
    <div class="compare" style="top:251px">
      <div class="photo before" role="img" aria-label="Overgrown lawn before landscaping" style="left:0"></div>
      <div class="photo after" role="img" aria-label="Finished garden path with flower beds" style="left:142px"></div>
      <span class="handle"></span>
    </div>

    <div class="photo thumb" role="img" aria-label="Garden path between hedges" style="left:81px;top:431px;background:radial-gradient(ellipse 30% 40% at 50% 80%,rgba(200,195,180,.8),transparent 70%),linear-gradient(160deg,#8fb15c,#3f6a25)"></div>
    <div class="photo thumb" role="img" aria-label="Garden with colorful flower beds" style="left:155px;top:431px;background:radial-gradient(ellipse 35% 25% at 30% 60%,rgba(220,110,140,.8),transparent 70%),radial-gradient(ellipse 30% 25% at 75% 75%,rgba(240,200,90,.6),transparent 70%),linear-gradient(160deg,#6f9a45,#3f6a25)"></div>
    <div class="photo thumb" role="img" aria-label="House front with manicured lawn" style="left:81px;top:504px;background:linear-gradient(180deg,#cfc6b0,#a8a088 40%,#7ea152 60%,#4b7a2c)"></div>
    <div class="photo thumb" role="img" aria-label="Formal garden with fountain" style="left:155px;top:504px;background:radial-gradient(ellipse 12% 30% at 55% 40%,rgba(230,240,240,.8),transparent 70%),linear-gradient(180deg,#3f5a30,#3a6a2a 50%,#8cb35a)"></div>
    <div class="photo projects" role="img" aria-label="Lit house and garden at dusk"></div>
    <div class="projects-title">Projects</div>
    <div class="projects-sub">All Projects</div>

    <div class="abs quote">
      <h2>Get a Free Estimate</h2>
      <span class="form-label" style="left:83px;top:72px">Your Info</span>
      <span class="form-label" style="left:192px;top:72px">Services Needed</span>
      <div class="field" style="top:83px">Name</div>
      <div class="field" style="top:98px">Phone</div>
      <div class="field" style="top:113px">Address</div>
      <div class="field" style="top:128px">Email</div>
      <div class="check" style="top:84px"><i></i>Lawn Care</div>
      <div class="check" style="top:93px"><i></i>Landscaping</div>
      <div class="check" style="top:102px"><i></i>Leaf Removal</div>
      <div class="check" style="top:111px"><i></i>Snow Removal</div>
    </div>
    <div class="submit">SUBMIT REQUEST</div>
    <div class="photo worker" role="img" aria-label="Gardener in orange cap tending a flower garden"></div>

    <footer class="abs footer">
      <div class="cta"><span class="cta-text">Contact us now to get quote</span><span class="cta-btn">Give me free quote</span></div>
      <div class="foot-col" style="left:83px">
        <h5>Contact Us</h5>
        <div class="foot-line"><svg width="4" height="4" viewBox="0 0 4 4"><rect x=".4" y=".4" width="3.2" height="3.2" rx=".8" fill="none" stroke="#2db93b" stroke-width=".6"/></svg>1-555-456-789</div>
        <div class="foot-line"><svg width="4" height="4" viewBox="0 0 4 4"><rect x=".3" y=".8" width="3.4" height="2.4" fill="none" stroke="#2db93b" stroke-width=".6"/></svg>info@example.com</div>
        <div class="foot-line"><svg width="4" height="4" viewBox="0 0 4 4"><circle cx="2" cy="1.6" r="1.2" fill="none" stroke="#2db93b" stroke-width=".6"/><path d="M2 2.8V4" stroke="#2db93b" stroke-width=".6"/></svg>Your address goes here</div>
        <div class="socials"><i></i><i></i><i></i></div>
      </div>
      <div class="foot-col" style="left:156px">
        <h5>About Us</h5>
        <div class="foot-link">Home</div><div class="foot-link">About</div><div class="foot-link">Blog</div><div class="foot-link">Contact</div>
      </div>
      <div class="foot-col" style="left:229px">
        <h5>Popular Services</h5>
        <div class="foot-link">Landscaping</div><div class="foot-link">Hardscaping</div><div class="foot-link">Irrigation</div><div class="foot-link">Landscape Design</div>
      </div>
      <div class="foot-col" style="left:302px">
        <h5>Emergency Service</h5>
        <div class="foot-line"><svg width="5" height="7" viewBox="0 0 5 7"><rect x=".4" y=".4" width="4.2" height="6.2" rx=".8" fill="none" stroke="#2db93b" stroke-width=".6"/></svg>1-555-456-789</div>
      </div>
      <div class="foot-brand"><span class="brand-mark"></span>Verdell Tree Care</div>
    </footer>
  </section>

</div>
</body>
</html>
```